Design a website for our small self storage business

We're looking for a freelance web designer who can produce a good-looking design for our small business website (no coding necessary). We will provide a list of pages to design, along with content outlines.

Key skills:
- Graphic design
- Responsive web design
- Proficiency with a modern web design tool such as Figma, Adobe Xd, or InVision

Please send relevant previous work (preferably in an inspectable format such as Figma or Invision).

```html
<!DOCTYPE html>
<html lang="en">
<head>
<meta charset="utf-8">
<title>Crestway Self Storage Valley Glen</title>
<link href="https://fonts.googleapis.com/css2?family=Poppins:wght@300;400;500;600;700;800&display=swap" rel="stylesheet">
<style>
:root{
  --blue:#0c57a4;
  --navy:#0d4e92;
  --navy-bar:#1460ac;
  --red:#e31b23;
  --grey:#eeeeee;
  --ink:#333333;
  --white:#ffffff;
}
*{box-sizing:border-box;margin:0;padding:0}
html,body{width:1200px;height:3428px;overflow:hidden}
body{position:relative;font-family:'Poppins',sans-serif;color:var(--ink);background:var(--white)}
.abs{position:absolute}
.brand{position:absolute;display:flex;align-items:center;gap:10px;font-family:'Poppins',sans-serif;font-weight:700;text-transform:uppercase;line-height:1.05}
.brand-mark{background:var(--red);flex:none}
.site-header .brand{left:75px;top:40px;color:var(--blue);font-size:30px}
.site-header .brand .brand-mark{width:22px;height:22px}
.nav{position:absolute;top:58px;left:403px;display:flex;gap:38px;font-size:16px;font-weight:500;text-transform:uppercase;color:#333}
.nav .active{color:var(--red);font-weight:600}
.call{position:absolute;left:858px;top:42px;display:flex;gap:14px;align-items:center}
.call-icon{width:44px;height:44px;border-radius:50%;background:var(--blue);display:flex;align-items:center;justify-content:center}
.call small{display:block;font-size:17px;font-weight:600;color:#222;line-height:1.1}
.call strong{display:block;font-size:26px;font-weight:700;color:var(--red);letter-spacing:.5px;line-height:1.2}
.hero{position:absolute;left:0;top:133px;width:1200px;height:735px;background:linear-gradient(100deg,#8a8f96 0%,#b9bcbf 30%,#6f7a86 60%,#3d4c63 100%)}
.hero-text{position:absolute;right:70px;top:215px;width:640px;text-align:right;color:var(--white)}
.hero h1{font-size:45px;font-weight:800;line-height:58px;text-transform:uppercase}
.hero h1 span{display:block;font-weight:500}
.hero p{font-size:17px;line-height:29px;margin-top:18px;width:515px;margin-left:auto}
.btn{display:inline-block;background:var(--red);color:var(--white);font-weight:700;text-transform:uppercase;text-align:center}
.hero .btn{margin-top:26px;width:217px;height:59px;line-height:55px;font-size:20px;border:2px solid var(--white)}
.sec-title{position:absolute;display:flex;align-items:center;justify-content:center;gap:22px;color:var(--blue);font-weight:700;text-transform:uppercase}
.sec-title::before,.sec-title::after{content:"";width:88px;height:2px;background:var(--blue);flex:none}
.card{position:absolute;top:1015px;width:329px;height:313px;background:var(--white);border-radius:8px;box-shadow:0 2px 14px rgba(0,0,0,.12);text-align:center}
.card.is-active{border:3px solid var(--red)}
.card-icon{width:120px;height:120px;border-radius:50%;margin:25px auto 0;background:linear-gradient(180deg,#d91c2a,#1a4d98);display:flex;align-items:center;justify-content:center}
.card h3{margin-top:28px;font-size:23px;font-weight:600;color:var(--blue);text-transform:uppercase}
.card p{margin:8px 28px 0;font-size:15.5px;line-height:28px;color:#444}
.feature-title{position:absolute;width:603px;font-size:37px;line-height:49px;font-weight:700;color:var(--blue);text-transform:uppercase;text-align:center}
.rule{position:absolute;height:2px;background:var(--blue)}
.feature p{font-size:17.5px;line-height:30.5px;text-align:center;color:#444}
.feature .btn{width:208px;height:57px;line-height:57px;font-size:18px}
.photo{position:absolute;border:6px solid var(--white);box-shadow:0 3px 12px rgba(0,0,0,.2)}
.footer-links h4,.footer-address h4{font-size:18px;font-weight:600;color:var(--white);text-transform:uppercase}
.footer-links a{display:block;color:var(--white);font-size:15px;text-decoration:none;margin-top:17px}
.footer-address{color:var(--white);font-size:15.5px}
.footer-address .name{font-size:18px;font-weight:600;margin-top:14px}
.footer-address .row{display:flex;gap:14px;margin-top:8px;line-height:27px}
.footer-address .row i{width:18px;flex:none;display:flex;padding-top:6px}
.site-footer .brand{left:75px;top:3055px;color:var(--white);font-size:34px}
.site-footer .brand .brand-mark{width:26px;height:26px;background:var(--white)}
.bottom-bar{position:absolute;left:0;top:3366px;width:1200px;height:62px;background:var(--navy-bar);color:var(--white);font-size:14.5px}
.social{position:absolute;top:18px;display:flex;gap:24px;left:916px}
.social span{width:22px;height:22px;border-radius:4px;background:var(--white)}
</style>
</head>
<body>

<header class="site-header">
  <div class="brand"><span class="brand-mark"></span>Crestway<br>Storage</div>
  <nav class="nav"><span class="active">Home</span><span>Units</span><span>Pay Online</span><span>Contact Us</span></nav>
  <div class="call">
    <div class="call-icon"><svg width="20" height="20" viewBox="0 0 24 24"><path fill="#fff" d="M6.6 10.8a15 15 0 0 0 6.6 6.6l2.2-2.2c.3-.3.7-.4 1-.2 1.1.4 2.3.6 3.6.6.6 0 1 .4 1 1V20c0 .6-.4 1-1 1C10.6 21 3 13.4 3 4c0-.6.4-1 1-1h3.5c.6 0 1 .4 1 1 0 1.3.2 2.5.6 3.6.1.3 0 .7-.2 1z"/></svg></div>
    <div><small>CALL US:</small><strong>1-800-555-0142</strong></div>
  </div>
</header>

<section class="hero" role="img" aria-label="Photo of open self storage units with a bicycle, mattress and cardboard boxes">
  <div class="hero-text">
    <h1>Welcome to Crestway<span>Self Storage Valley Glen</span></h1>
    <p>Crestway Self Storage located on Linden Ave. between Maple Ave. and Birch Ave. near the Civic Center in the valley.</p>
    <span class="btn">See Our Units</span>
  </div>
</section>
<svg class="abs" style="left:0;top:740px" width="1200" height="130"><polygon points="0,129 778,8 1200,129" fill="#fff"/></svg>

<div class="sec-title" style="left:0;width:1200px;top:913px;font-size:38px">Key Advantages</div>

<article class="card is-active" style="left:75px">
  <div class="card-icon"><svg width="56" height="56" viewBox="0 0 24 24" fill="none" stroke="#fff" stroke-width="1.3"><rect x="5" y="2" width="12" height="16" rx="1"/><path d="M8 6h6M8 9h6M8 12h4"/><circle cx="18" cy="18" r="3.5"/></svg></div>
  <h3>Affordable</h3>
  <p>Sed ut perspiciatis unde omnis iste natus error sit voluptatem accu santium doloremque.</p>
</article>
<article class="card" style="left:437px">
  <div class="card-icon"><svg width="56" height="56" viewBox="0 0 24 24" fill="none" stroke="#fff" stroke-width="1.3"><rect x="4" y="10" width="14" height="10" rx="1"/><path d="M7 10V7a4 4 0 0 1 8 0v3"/><circle cx="18" cy="18" r="3.5"/><path d="M16.5 18l1 1 2-2"/></svg></div>
  <h3>Secure</h3>
  <p>Sed ut perspiciatis unde omnis iste natus error sit voluptatem accu santium doloremque.</p>
</article>
<article class="card" style="left:798px">
  <div class="card-icon"><svg width="56" height="56" viewBox="0 0 24 24" fill="none" stroke="#fff" stroke-width="1.3"><circle cx="13" cy="8" r="4.5"/><path d="M2 17l5-2h6l5-3 2 1-7 6H6l-4 1"/></svg></div>
  <h3>Convenient</h3>
  <p>Sed ut perspiciatis unde omnis iste natus error sit voluptatem accu santium doloremque.</p>
</article>

<svg class="abs" style="left:0;top:1375px" width="1200" height="745"><polygon points="0,0 425,122 1200,0 1200,620 425,745 0,620" fill="#eeeeee"/></svg>

<section class="feature">
  <span class="rule" style="left:76px;top:1655px;width:86px"></span>
  <span class="rule" style="left:588px;top:1655px;width:90px"></span>
  <h2 class="feature-title" style="left:75px;top:1631px">Just Show Up With<br>Your Stuff</h2>
  <p class="abs" style="left:88px;width:580px;top:1744px">Sed ut perspiciatis unde omnis iste natus error sit voluptatem accusantium doloremque laudantium, totam rem aperiam, eaque ipsa quae ab illo inventore veritatis et quasi architecto beatae vitae dicta sunt explicabo. Nemo enim ipsam voluptatem quia voluptas sit aspernatur aut odit aut fugit, sed quia consequuntur magni dolores.</p>
  <span class="btn abs" style="left:273px;top:1957px">Read More</span>
  <div class="abs" style="left:766px;top:1540px;width:360px;height:344px;background:var(--red)"></div>
  <div class="photo" style="left:704px;top:1575px;width:393px;height:512px;background:linear-gradient(135deg,#5d6f88,#d9633d 50%,#c9946a)" role="img" aria-label="Photo of a hand placing a red binder on a shelf"></div>
</section>

<section class="feature">
  <div class="abs" style="left:75px;top:2193px;width:360px;height:347px;background:var(--red)"></div>
  <div class="photo" style="left:105px;top:2228px;width:392px;height:515px;background:linear-gradient(90deg,#b3262b,#d8424a 35%,#8f7d6a 55%,#c8373e 75%,#a22329)" role="img" aria-label="Photo of a corridor lined with red storage unit doors"></div>
  <span class="rule" style="left:520px;top:2296px;width:87px"></span>
  <span class="rule" style="left:1032px;top:2296px;width:91px"></span>
  <h2 class="feature-title" style="left:520px;top:2272px">What Should I<br>Bring To Rent A Space?</h2>
  <p class="abs" style="left:530px;width:582px;top:2383px">Sed ut perspiciatis unde omnis iste natus error sit voluptatem accusantium doloremque laudantium, totam rem aperiam, eaque ipsa quae ab illo inventore veritatis et quasi architecto beatae vitae dicta sunt explicabo. Nemo enim ipsam voluptatem quia voluptas sit aspernatur aut odit aut fugit, sed quia consequuntur magni dolores.</p>
  <span class="btn abs" style="left:717px;top:2597px">Read More</span>
</section>

<footer class="site-footer">
  <svg class="abs" style="left:0;top:2823px" width="1200" height="545"><polygon points="0,0 425,118 1200,0 1200,545 0,545" fill="#0d4e92"/></svg>
  <div class="brand"><span class="brand-mark"></span>Crestway<br>Storage</div>
  <div class="footer-links abs" style="left:337px;top:2990px">
    <h4>Quick Links</h4>
    <a>Home</a><a>Units</a><a>Pay Online</a><a>Contact Us</a>
  </div>
  <div class="footer-address abs" style="left:522px;top:2990px;width:280px">
    <h4>Address</h4>
    <div class="name">Crestway Self Storage</div>
    <div class="row"><i><svg width="14" height="14" viewBox="0 0 24 24"><path fill="#fff" d="M12 2a7 7 0 0 0-7 7c0 5 7 13 7 13s7-8 7-13a7 7 0 0 0-7-7z"/></svg></i><span>2840 Linden Avenue Valley Glen, CA 91405</span></div>
    <div class="row"><i><svg width="14" height="14" viewBox="0 0 24 24"><path fill="#fff" d="M6.6 10.8a15 15 0 0 0 6.6 6.6l2.2-2.2c.3-.3.7-.4 1-.2 1.1.4 2.3.6 3.6.6.6 0 1 .4 1 1V20c0 .6-.4 1-1 1C10.6 21 3 13.4 3 4c0-.6.4-1 1-1h3.5c.6 0 1 .4 1 1 0 1.3.2 2.5.6 3.6z"/></svg></i><span>1-800-555-0142</span></div>
    <div class="row"><i><svg width="14" height="14" viewBox="0 0 24 24"><rect x="3" y="8" width="18" height="12" rx="1" fill="#fff"/><rect x="7" y="3" width="10" height="6" fill="#fff"/></svg></i><span>1-800-555-0142</span></div>
    <div class="row"><i><svg width="14" height="14" viewBox="0 0 24 24"><path fill="#fff" d="M2 5h20v14H2z"/><path d="M2 5l10 8 10-8" stroke="#0d4e92" stroke-width="2" fill="none"/></svg></i><span>hello@crestwaystorage.com</span></div>
    <h4 style="margin-top:22px">Opening Times</h4>
    <div style="margin-top:6px;font-size:15px">9:30 AM - 5:30 PM, 7 days a week</div>
  </div>
  <div class="abs" style="left:823px;top:3003px;width:303px;height:317px;background:linear-gradient(135deg,#eef0f2,#dfe3e8)" role="img" aria-label="Street map showing the storage facility location"></div>
  <div class="bottom-bar">
    <span class="abs" style="left:75px;top:20px">© Copyright 2022 Crestway Storage All Rights Reserved</span>
    <div class="social" aria-label="Social media links"><span></span><span></span><span></span><span></span><span></span></div>
  </div>
</footer>

</body>
</html>
```